Beacon Advisory Website

I currently have a website www.beaconadvisoryinc.com. We are a IT Consulting Company. Our website will pretty much tell out our services. I am looking to enhance my website and make it look more professional. Looking for very classy and Contemporary look and design for my website.

It Company

```html
<!DOCTYPE html>
<html lang="en">
<head>
<meta charset="utf-8">
<title>Beacon Advisory</title>
<link href="https://fonts.googleapis.com/css2?family=Lato:wght@300;400;700&family=Open+Sans:wght@400;700;800&display=swap" rel="stylesheet">
<style>
:root{
  --blue:#1a63a8;
  --navy:#14508f;
  --sky:#1e9ad6;
  --ink:#1d2a38;
  --text:#555;
  --muted:#8a8a8a;
  --grey-bg:#f4f4f4;
  --white:#fff;
}
*{margin:0;padding:0;box-sizing:border-box}
html,body{width:840px;height:1200px;overflow:hidden}
body{position:relative;font-family:'Lato',sans-serif;color:var(--text);background:var(--white)}
.abs{position:absolute}

/* header + hero backdrop */
.hero-backdrop{left:0;top:0;width:840px;height:412px;background:linear-gradient(180deg,#f3f5f7 0%,#e9edf0 60%,#f6f7f8 100%)}
.topbar{left:0;top:7px;width:840px;height:14px;font-size:7px;font-weight:700;letter-spacing:.3px}
.social-dots{left:82px;top:3px;display:flex;gap:9px}
.social-dots span{width:7px;height:7px;border-radius:50%;background:#666}
.question{left:154px;top:3px;color:#555}
.question b{color:var(--blue)}
.util{right:104px;top:2px;display:flex;gap:16px;color:#444;font-size:7.5px}
.search-box{left:743px;top:4px;width:19px;height:18px;background:#888}
.logo{left:66px;top:32px;display:flex;align-items:center;gap:7px}
.logo .mark{width:34px;height:34px;border-radius:50%;background:var(--blue)}
.logo .name{font-size:16px;font-weight:700;color:var(--navy);line-height:1}
.nav{left:381px;top:46px;display:flex;font-size:8.5px;font-weight:700;color:#333;letter-spacing:.2px}
.nav a{display:block;height:18px;line-height:18px;padding:0 10px;margin-right:1px;color:#333;text-decoration:none}
.nav a.active{background:var(--blue);color:var(--white)}
.free-quote{left:725px;top:36px;width:37px;height:38px;background:var(--sky);color:var(--white);text-align:center;padding-top:7px;font-family:'Open Sans',sans-serif}
.free-quote b{display:block;font-size:10px;font-weight:800;line-height:1}
.free-quote small{font-size:6.5px;font-weight:700}

/* slider */
.slider{left:78px;top:91px;width:683px;height:287px;background:var(--white);padding:2px 2px 0}
.slider-photo{width:679px;height:279px;background:linear-gradient(135deg,#dfe6ec 0%,#c9d3dc 45%,#7e8a96 100%)}
.slider-bar{left:0;bottom:0;width:683px;height:6px;background:var(--blue)}
.slider-dots{right:30px;top:16px;display:flex;gap:8px}
.slider-dots span{width:14px;height:2px;background:rgba(255,255,255,.5)}
.slider-dots span.on{background:var(--white)}
.tag{left:12px;top:189px;background:var(--sky);color:var(--white);font-size:8.5px;padding:4px 6px}
.headline{left:12px;top:220px;color:var(--white);font-family:'Open Sans',sans-serif;font-weight:800;font-size:19px;line-height:23px;letter-spacing:.2px}
.next{left:455px;top:242px;width:20px;height:20px;border:1.5px solid var(--white);border-radius:50%}

/* about */
.section-title{width:840px;left:0;text-align:center;font-size:18px;font-weight:700;color:var(--ink);letter-spacing:.5px}
.section-sub{width:840px;left:0;text-align:center;font-size:14px;font-weight:300;color:#333}
.about-copy{left:70px;top:500px;width:702px;text-align:center;font-size:9.4px;line-height:14.4px;color:#555;letter-spacing:.15px}
.btn{height:26px;line-height:26px;text-align:center;color:var(--white);font-size:9px}
.btn-read{left:332px;top:576px;width:83px;background:var(--sky)}
.btn-contact{left:424px;top:576px;width:83px;background:var(--blue)}

/* services */
.services{left:0;top:657px;width:840px;height:295px;background:var(--grey-bg)}
.divider{left:275px;top:753px;width:276px;height:1px;background:#e2e2e2}
.divider-accent{left:352px;top:752px;width:122px;height:2px;background:#8fd0ee}
.service{width:220px;text-align:center}
.service h3{font-size:11.5px;font-weight:700;color:var(--ink);letter-spacing:.6px;margin-top:10px}
.service p{font-size:8.6px;font-weight:300;line-height:12px;color:var(--muted);margin-top:8px;height:36px}
.service .more{display:inline-flex;align-items:center;gap:4px;margin-top:6px;font-size:9px;color:var(--blue)}
.service .more i{width:9px;height:9px;border:1px solid var(--blue);border-radius:50%}
.service svg{display:block;margin:0 auto}

/* footer */
.footer{left:0;top:952px;width:840px;height:248px;background:var(--blue);color:var(--white)}
.f-head{top:30px;font-size:8.5px;letter-spacing:.6px}
.f-list{top:60px;font-size:8.2px;line-height:21.5px}
.f-links{top:60px;font-size:7.2px;line-height:21.5px}
.contact-row{left:384px;width:160px;font-size:7.8px;line-height:13px;display:flex;gap:8px;border-bottom:1px solid rgba(255,255,255,.12);padding-bottom:10px}
.contact-row svg{flex:none;margin-top:2px}
.f-social{left:386px;top:166px;display:flex;gap:14px}
.f-social span{width:10px;height:10px;border-radius:50%;background:#9cc0e2}
.field{left:610px;width:160px;background:#2470b6;font-size:6.8px;padding:6px 7px}
.send{left:682px;top:1117px;width:88px;height:19px;line-height:19px;background:var(--sky);text-align:center;font-size:7px;color:var(--white)}
.f-rule{left:72px;top:1162px;width:696px;height:1px;background:rgba(255,255,255,.12)}
.copyright{left:0;top:1175px;width:840px;text-align:center;font-size:7.5px;font-weight:700;color:var(--white)}
</style>
</head>
<body>

<div class="abs hero-backdrop"></div>

<div class="abs topbar">
  <div class="abs social-dots"><span></span><span></span><span></span></div>
  <div class="abs question">QUESTIONS? <b>CALL: 0800 555 210</b></div>
  <div class="abs util"><span>LANGUAGES</span><span>SUPPORT</span><span>LOG IN</span></div>
</div>
<div class="abs search-box"></div>

<div class="abs logo"><span class="mark"></span><span class="name">Beacon Advisory</span></div>

<nav class="abs nav">
  <a class="active">HOMEPAGES</a><a>ABOUT US</a><a>SERVICES</a><a>FEATURES</a><a>CONTACT US</a>
</nav>
<div class="abs free-quote"><b>FREE</b><small>QUOTE</small></div>

<div class="abs slider">
  <div class="slider-photo" role="img" aria-label="Photo of three consultants reviewing documents together at a desk"></div>
  <div class="abs slider-dots"><span></span><span class="on"></span></div>
  <div class="abs tag">RICH FEATURED</div>
  <div class="abs headline">PACKED WITH A HUGE VARIATY<br>OF SLIDERS FOR MANY DIFFERENT PURPOSES</div>
  <div class="abs next"><svg width="17" height="17" viewBox="0 0 17 17"><path d="M7 5l3.5 3.5L7 12" fill="none" stroke="#fff" stroke-width="1.4"/></svg></div>
  <div class="abs slider-bar"></div>
</div>

<h2 class="abs section-title" style="top:447px">ABOUT US</h2>
<p class="abs section-sub" style="top:467px">Integer vitae libero ac risus egestas placerat</p>
<p class="abs about-copy">Today’s IT market is a dynamic, fast-paced industry, with ever-increasing demands. Meeting these demands for over 25 years, Beacon Advisory maintains a global presence, aggressively recruiting expertly qualified IT and Management Professionals from around the world and cultivating key partnerships with corporations to understand their business models end-to-end, with a goal of delivering exceptional client service and ensuring a consistent delivery of the talent needed to drive results.</p>
<div class="abs btn btn-read">READ MORE</div>
<div class="abs btn btn-contact">CONTACT US</div>

<section class="abs services"></section>
<h2 class="abs section-title" style="top:693px">OUR SERVICES</h2>
<p class="abs section-sub" style="top:713px">Integer vitae libero ac risus egestas placerat</p>
<div class="abs divider"></div>
<div class="abs divider-accent"></div>
<svg class="abs" style="left:405px;top:753px" width="16" height="8" viewBox="0 0 16 8"><path d="M0 0l8 7 8-7" fill="#f4f4f4" stroke="#8fd0ee" stroke-width="1.4"/></svg>

<div class="abs service" style="left:64px;top:779px">
  <svg width="36" height="38" viewBox="0 0 36 38"><ellipse cx="19" cy="7" rx="10" ry="6" fill="#1e9ad6"/><circle cx="8" cy="20" r="4.5" fill="#1a63a8"/><rect x="2" y="26" width="12" height="12" rx="3" fill="#1a63a8"/><circle cx="28" cy="20" r="4.5" fill="#1a63a8"/><rect x="22" y="26" width="12" height="12" rx="3" fill="#1a63a8"/></svg>
  <h3>CONSULTING</h3>
  <p>Beacon Advisory has certified professional consultants to work with you to help increase the business by providing IT services ...</p>
  <span class="more">Read More <i></i></span>
</div>
<div class="abs service" style="left:309px;top:779px">
  <svg width="40" height="38" viewBox="0 0 40 38"><circle cx="20" cy="5" r="4.5" fill="#1e9ad6"/><rect x="14" y="10" width="12" height="9" rx="2" fill="#1e9ad6"/><circle cx="10" cy="24" r="4.5" fill="#1a63a8"/><rect x="3" y="29" width="14" height="9" rx="2" fill="#1a63a8"/><circle cx="30" cy="24" r="4.5" fill="#1a63a8"/><rect x="23" y="29" width="14" height="9" rx="2" fill="#1a63a8"/></svg>
  <h3>STAFF AUGMENTATION</h3>
  <p>For years Beacon Advisory as been offering our customers the ability to augment their existing staff ...</p>
  <span class="more">Read More <i></i></span>
</div>
<div class="abs service" style="left:556px;top:779px">
  <svg width="40" height="40" viewBox="0 0 40 40"><circle cx="21" cy="18" r="16" fill="none" stroke="#1a63a8" stroke-width="3"/><circle cx="21" cy="18" r="9" fill="#1e9ad6"/><path d="M16 23L4 36" stroke="#1a63a8" stroke-width="5" stroke-linecap="round"/></svg>
  <h3>OFFSHORE</h3>
  <p>Our Offshore development model has a unique distinction of providing efficient software solutions ...</p>
  <span class="more">Read More <i></i></span>
</div>

<footer class="abs footer">
  <div class="abs f-head" style="left:69px">ABOUT US</div>
  <div class="abs f-head" style="left:205px">LINKS</div>
  <div class="abs f-head" style="left:384px">CONTACT INFO</div>
  <div class="abs f-head" style="left:610px">CONTACT US</div>

  <div class="abs f-list" style="left:69px">FAQ’s<br>Privacy Policy<br>Terms &amp; Conditions<br>Contact Us</div>
  <div class="abs f-links" style="left:205px">HOMEPAGES<br>ABOUT US<br>SERVICES<br>FEATURES<br>CONTACT US</div>

  <div class="abs contact-row" style="top:58px"><svg width="10" height="8" viewBox="0 0 10 8"><rect x=".5" y=".5" width="9" height="7" fill="none" stroke="#fff"/><path d="M.5 .5L5 4.5 9.5 .5" fill="none" stroke="#fff"/></svg><span>hello@beaconadvisory.example</span></div>
  <div class="abs contact-row" style="top:90px"><svg width="9" height="9" viewBox="0 0 9 9"><path d="M1 1c0 4 3 7 7 7l1-2-2-1-1 1C4 5 4 4 3 3l1-1-1-2z" fill="#fff"/></svg><span>Phone: +1 (555) 014 2290</span></div>
  <div class="abs contact-row" style="top:124px"><svg width="8" height="10" viewBox="0 0 8 10"><path d="M4 10S0 5.5 0 4a4 4 0 018 0c0 1.5-4 6-4 6z" fill="#fff"/><circle cx="4" cy="4" r="1.5" fill="#1a63a8"/></svg><span>48 Harbor Lane, Suite 310<br>Fairview, CT 06500</span></div>
  <div class="abs f-social"><span></span><span></span><span></span><span></span><span></span><span></span></div>
</footer>
<div class="abs field" style="top:1012px;height:20px">Name</div>
<div class="abs field" style="top:1035px;height:19px">Email Address</div>
<div class="abs field" style="top:1059px;height:47px">Message</div>
<div class="abs send">SEND</div>
<div class="abs f-rule"></div>
<div class="abs copyright">Copyright © 2016 - yoursite</div>

</body>
</html>
```